UK landscaping company needs website

We, Brackwell Landscapes need a website design for a company based in Surrey, UK. The design should be bold and playful. We have three main areas of work driveways, paving and fencing. It shouldn't be too heavy in text and concentrate on the pictures from previous jobs we've completed. You may use stock images for the design, these can be changed if you are successful. Please don’t just copy the flyer it is just there to provide content.
We have a logo design which we would also like editing slightly.
Here are some of my local competitors
https://www.pelmarlandscapes.example.co.uk/

https://www.twinfirgardendesign.example.com/

https://kestbyrnlandscapes.example.co.uk/

Industry/Entity Type

Landscaping

Coding

Coded - Design and coding required

Number of Pages Required

3 page

Font styles to use
Sans Serif

Requirements
Must have
• Pictures of my previous jobs.
Must be mobile friendly
Easy to navigate
Nice to have
• Try to use different colours. It would be good to have some designs that aren’t just black and green.
I’d like some curves in the design.
Should not have
• We install hard landscaping. Think more building/construction and less plants and cutting grass.

```html
<!DOCTYPE html>
<html lang="en">
<head>
<meta charset="utf-8">
<title>Brackwell Landscapes</title>
<link rel="stylesheet" href="https://fonts.googleapis.com/css2?family=Libre+Baskerville:wght@400;700&family=Roboto:wght@400;500;700&family=Montserrat:wght@600;700&display=swap">
<style>
:root{
  --green:#5aae2e;
  --green-dark:#3f8a1c;
  --forest:#0f3526;
  --ink:#1c1c1c;
  --grey-text:#6b6b6b;
  --panel:#e9e9e9;
  --black:#050505;
  --white:#ffffff;
}
*{margin:0;padding:0;box-sizing:border-box}
html,body{width:1200px;height:4166px;overflow:hidden}
body{position:relative;background:var(--white);font-family:"Roboto",Arial,sans-serif;color:var(--ink)}
.abs{position:absolute}
.serif{font-family:"Libre Baskerville",Georgia,serif}
.center{text-align:center}
.accent{color:var(--green)}

/* top bar */
.topbar{left:0;top:0;width:1200px;height:36px;background:var(--forest);color:var(--white);font-size:14px;font-weight:500}
.topbar .phone{left:114px;top:10px}
.topbar .mail{left:308px;top:10px}
.topbar .sep{left:262px;top:6px;width:1px;height:24px;background:#6d8a7d}
.topbar .social{right:112px;top:12px;display:flex;gap:9px}
.dot{width:11px;height:11px;border-radius:50%;background:var(--white)}

/* nav */
.nav{left:0;top:36px;width:1200px;height:87px;background:var(--white)}
.brand{left:110px;top:20px;font-family:"Roboto",Arial,sans-serif;font-weight:700;color:var(--green);font-size:26px;line-height:1;letter-spacing:.5px}
.brand small{display:block;font-size:12px;letter-spacing:2px;margin-top:4px}
.menu{left:352px;top:36px;display:flex;gap:37px;font-size:14px;font-weight:500;color:var(--ink)}
.btn{display:inline-block;border-radius:30px;font-weight:700;text-align:center}
.quote-btn{left:935px;top:17px;width:152px;height:52px;line-height:52px;background:var(--green);color:var(--white);font-size:16px}

/* hero */
.hero{left:0;top:123px;width:1200px;height:597px;background:linear-gradient(180deg,#5c5f5d 0%,#6f716e 40%,#8a8b86 75%,#7b7c78 100%)}
.hero h1{left:0;top:170px;width:1200px;font-weight:400;font-size:70px;color:var(--white)}
.hero p{left:240px;top:262px;width:720px;font-size:16px;font-weight:700;line-height:26px;color:var(--white)}
.start-btn{left:522px;top:335px;width:152px;height:50px;line-height:50px;background:var(--white);color:var(--green);font-size:16px;font-weight:500}
.hero-curve{left:0;top:640px;width:1200px;height:85px}

/* areas */
.areas h2{left:0;top:808px;width:1200px;font-size:41px;font-weight:400;color:var(--forest)}
.areas .lead{left:230px;top:868px;width:740px;font-size:16px;font-weight:700;line-height:26px}
.area{width:330px;text-align:center;top:949px}
.area .photo{width:246px;height:246px;border-radius:50%;border:4px solid var(--green);margin:0 auto}
.area h3{font-family:"Libre Baskerville",Georgia,serif;font-weight:400;font-size:20px;margin-top:22px}
.area p{font-size:13px;color:#333;line-height:26px;margin-top:14px;width:230px;margin-left:auto;margin-right:auto}
.chev{width:26px;height:56px}

/* about */
.about{left:0;top:1429px;width:1200px;height:557px;background:var(--panel)}
.about .kicker{left:110px;top:92px;color:var(--green);font-size:16px;font-weight:500}
.about h2{left:108px;top:120px;font-size:37px;font-weight:400;color:var(--forest)}
.about p{left:110px;top:178px;width:385px;font-size:15px;line-height:26px;color:var(--grey-text)}
.read-btn{left:110px;top:409px;width:152px;height:51px;line-height:51px;background:var(--green);color:var(--white);font-size:16px;font-weight:500}
.about .frame{left:608px;top:112px;width:451px;height:340px;background:var(--green)}
.about .photo{left:600px;top:104px;width:451px;height:340px;background:linear-gradient(160deg,#8a5a3c 0%,#a97a55 30%,#bdbdb7 55%,#cfcfca 100%)}

/* stats */
.stats{left:0;top:1986px;width:1200px;height:258px;background:linear-gradient(90deg,#5ea732 0%,#66ad35 60%,#74b444 100%)}
.stat{width:171px;text-align:center;top:0}
.stat .num{font-family:"Montserrat",Arial,sans-serif;font-weight:700;font-size:27px;color:var(--forest);margin-top:87px}
.stat svg{display:block;margin:22px auto 0}
.stat-label{width:171px;height:45px;line-height:45px;background:var(--forest);color:var(--white);font-family:"Montserrat",Arial,sans-serif;font-weight:700;font-size:17px;text-align:center;top:2225px}

/* gallery */
.gallery h2{left:0;top:2356px;width:1200px;font-size:39px;font-weight:400;color:var(--forest)}
.before{left:183px;top:2434px;width:412px;height:391px;background:linear-gradient(180deg,#3a4a2c 0%,#4b5e34 50%,#5f7b3c 75%,#4d5a45 100%)}
.after{left:600px;top:2434px;width:409px;height:391px;background:linear-gradient(180deg,#9c7a3e 0%,#b08c4c 60%,#a99f8a 88%,#7e9b4e 100%)}
.ba-label{top:2620px;font-family:"Libre Baskerville",Georgia,serif;font-size:22px;color:var(--white)}
.ba-knob{left:564px;top:2601px;width:64px;height:64px;border-radius:50%;background:var(--green)}
.thumbs{left:183px;top:2833px;display:flex;gap:11px}
.thumb{width:129px;height:89px}

/* testimonial */
.testi{left:0;top:3017px;width:1200px;height:600px;background:var(--panel)}
.testi h2{left:0;top:90px;width:1200px;font-size:38px;font-weight:400;color:var(--forest)}
.testi .lead{left:230px;top:157px;width:740px;font-size:16px;line-height:26px;color:#444}
.testi .face{left:217px;top:229px;width:252px;height:252px;border-radius:50%;border:4px solid var(--green);background:radial-gradient(circle at 50% 40%,#b58a6c 0%,#8a6249 45%,#d8d8d8 75%)}
.testi blockquote{left:540px;top:258px;width:442px;text-align:right;font-style:italic;font-size:16px;line-height:26px;color:#444}
.testi .who{left:700px;top:397px;width:282px;text-align:right;font-style:italic;font-size:16px;color:var(--green)}
.testi .arrows{left:942px;top:441px;display:flex;gap:26px;font-size:18px;color:#444}

/* footer */
.footer{left:0;top:3600px;width:1200px;height:566px;background:var(--black)}
.footer-curve{left:0;top:3590px;width:1200px;height:70px}
.news-title{left:240px;top:3720px;color:var(--white);font-family:"Montserrat",Arial,sans-serif;font-weight:700;font-size:21px;line-height:25px;letter-spacing:.5px}
.news-box{left:427px;top:3718px;width:620px;height:52px;background:var(--white);border-radius:4px;border:2px solid var(--green)}
.news-input{position:absolute;left:13px;top:16px;font-size:13px;color:#777}
.sub-btn{position:absolute;right:4px;top:4px;width:145px;height:40px;line-height:40px;background:var(--green);color:var(--white);font-size:17px;font-weight:700;text-align:center;border-radius:3px}
.rule{left:110px;width:978px;height:1px;background:#666}
.foot-brand{left:140px;top:3878px;color:var(--white);font-family:"Roboto",Arial,sans-serif;font-weight:700;font-size:36px;line-height:40px;text-align:center;width:200px}
.foot-brand small{display:block;font-size:14px;letter-spacing:3px;line-height:20px}
.foot-social{left:183px;top:3999px;display:flex;gap:25px}
.foot-social .dot{width:13px;height:13px}
.col h4{font-family:"Libre Baskerville",Georgia,serif;font-weight:400;font-size:19px;color:var(--white);letter-spacing:.3px}
.col ul{list-style:none;margin-top:16px}
.col li{color:var(--white);font-size:13px;font-weight:700;line-height:26px;padding-left:22px;position:relative}
.col li:before{content:"»";position:absolute;left:0;top:-1px}
.contact li:before{content:none}
.contact li{padding-left:26px;margin-bottom:14px}
.contact svg{position:absolute;left:0;top:6px}
.copy{top:4085px;font-family:"Libre Baskerville",Georgia,serif;font-size:14px;color:var(--white)}
</style>
</head>
<body>

<header>
  <div class="abs topbar">
    <span class="abs phone">
      <svg width="11" height="11" viewBox="0 0 24 24" fill="#fff" style="vertical-align:-1px"><path d="M6.6 10.8a15 15 0 006.6 6.6l2.2-2.2c.3-.3.7-.4 1-.2 1.1.4 2.3.6 3.6.6.6 0 1 .4 1 1V20c0 .6-.4 1-1 1A17 17 0 013 4c0-.6.4-1 1-1h3.5c.6 0 1 .4 1 1 0 1.3.2 2.5.6 3.6.1.3 0 .7-.2 1z"/></svg>
      07700 900 418</span>
    <span class="abs sep"></span>
    <span class="abs mail">
      <svg width="12" height="10" viewBox="0 0 24 18" fill="#fff" style="vertical-align:-1px"><path d="M0 1l12 8 12-8v17H0z"/><path d="M0 0h24L12 7z"/></svg>
      info@brackwelllandscapes.example.com</span>
    <div class="abs social"><i class="dot"></i><i class="dot"></i><i class="dot"></i><i class="dot"></i></div>
  </div>

  <nav class="abs nav">
    <div class="abs brand">BRACKWELL<small>LANDSCAPES</small></div>
    <div class="abs menu"><span>HOME</span><span>ABOUT US</span><span>SERVICES</span><span>GALLERY</span><span>BLOG</span><span>CONTACT US</span></div>
    <span class="abs btn quote-btn">GET A QUOTE</span>
  </nav>
</header>

<section class="abs hero" role="img" aria-label="Photo of a grey slate chipping border with granite kerb edging and paved path">
  <h1 class="abs serif center">Brackwell Landscapes</h1>
  <p class="abs center">Lorem ipsum dolor sit amet, consectetur adipiscing elit, sed do eiusmod tempor incididunt ut labore et dolore magna aliqua.</p>
  <span class="abs btn start-btn">GET STARTED</span>
</section>
<svg class="abs hero-curve" viewBox="0 0 1200 85" preserveAspectRatio="none">
  <path d="M0 85 Q600 -20 1200 85 Z" fill="#ffffff"/>
  <path d="M0 80 Q600 -10 1200 80 L1200 70 Q600 -28 0 70 Z" fill="#5aae2e"/>
  <path d="M0 70 Q600 -28 1200 70 L1200 64 Q600 -34 0 64 Z" fill="#0f3526"/>
  <rect x="574" y="0" width="52" height="52" rx="26" fill="#ffffff"/>
  <rect x="589" y="14" width="22" height="32" rx="11" fill="none" stroke="#222" stroke-width="2"/>
  <line x1="600" y1="20" x2="600" y2="27" stroke="#222" stroke-width="2"/>
  <path d="M593 52 l7 6 7-6 M593 59 l7 6 7-6 M593 66 l7 6 7-6" fill="none" stroke="#222" stroke-width="1.6"/>
</svg>

<section class="areas">
  <h2 class="abs serif center">We have <span class="accent">areas of work</span></h2>
  <p class="abs lead center">Lorem ipsum dolor sit amet, consectetur adipiscing elit, sed do eiusmod tempor incididunt ut labore et dolore magna aliqua.</p>

  <svg class="abs chev" style="left:60px;top:1097px" viewBox="0 0 26 56"><path d="M22 2 L4 28 L22 54" fill="none" stroke="#222" stroke-width="2"/></svg>
  <svg class="abs chev" style="left:1114px;top:1097px" viewBox="0 0 26 56"><path d="M4 2 L22 28 L4 54" fill="none" stroke="#222" stroke-width="2"/></svg>

  <div class="abs area" style="left:105px">
    <div class="photo" role="img" aria-label="Photo of a block-paved driveway in red and charcoal tones" style="background:linear-gradient(160deg,#7d6f82 0%,#8a5f5a 45%,#5b5c6a 100%)"></div>
    <h3>DRIVEWAYS</h3>
    <p>Lorem ipsum dolor sit amet, consec tetur adipiscing elit, sed do eiusmod tempor incididunt ut.</p>
  </div>
  <div class="abs area" style="left:433px">
    <div class="photo" role="img" aria-label="Photo of a pale stone paved patio with timber pergola" style="background:linear-gradient(180deg,#6b4a36 0%,#8c7a66 40%,#cfcfcc 70%,#e0e0dd 100%)"></div>
    <h3>PAVING</h3>
    <p>Lorem ipsum dolor sit amet, consec tetur adipiscing elit, sed do eiusmod tempor incididunt ut.</p>
  </div>
  <div class="abs area" style="left:763px">
    <div class="photo" role="img" aria-label="Photo of a new timber panel fence with gravel border" style="background:linear-gradient(180deg,#4d6d34 0%,#7a5a32 25%,#8a6a3e 70%,#9a9a92 100%)"></div>
    <h3>FENCING</h3>
    <p>Lorem ipsum dolor sit amet, consec tetur adipiscing elit, sed do eiusmod tempor incididunt ut.</p>
  </div>
</section>

<section class="abs about">
  <span class="abs kicker">About Us</span>
  <h2 class="abs serif">Brackwell Landscapes</h2>
  <p class="abs">Lorem ipsum dolor sit amet, consectetur adipiscing elit, sed do eiusmod tempor incididunt ut labore et dolore m agna aliqua. Ut enim ad minim veniam, quis nostrud ex ercitation ullamco laboris nisi ut aliquip ex ea commo do consequat. Duis aute irure dolor in reprehenderit in voluptate velit esse cillum dolore eu fugiat nulla pariat ur. Excepteur sint occaecat cupidatat non proident, sunt in culpa qui officia .</p>
  <span class="abs btn read-btn">READ MORE</span>
  <div class="abs frame"></div>
  <div class="abs photo" role="img" aria-label="Photo of grey porcelain patio steps beside a timber fence"></div>
</section>

<section class="abs stats" role="img" aria-label="Green-tinted photo of a timber fence behind the figures"></section>
<div class="abs stat" style="left:143px;top:1986px"><div class="num">400 +</div>
  <svg width="80" height="80" viewBox="0 0 80 80"><circle cx="40" cy="40" r="37" fill="none" stroke="#0f3526" stroke-width="2.5"/><path d="M25 38h8v20h-8z M33 40l7-12c2-3 6-2 6 2l-1 8h9c3 0 4 3 3 5l-4 12c-1 2-2 3-4 3H33" fill="none" stroke="#0f3526" stroke-width="2.5" stroke-linejoin="round"/></svg></div>
<div class="abs stat" style="left:390px;top:1986px"><div class="num">400 +</div>
  <svg width="80" height="80" viewBox="0 0 80 80"><circle cx="40" cy="40" r="37" fill="none" stroke="#0f3526" stroke-width="2.5"/><path d="M25 38h8v20h-8z M33 40l7-12c2-3 6-2 6 2l-1 8h9c3 0 4 3 3 5l-4 12c-1 2-2 3-4 3H33" fill="none" stroke="#0f3526" stroke-width="2.5" stroke-linejoin="round"/></svg></div>
<div class="abs stat" style="left:636px;top:1986px"><div class="num">400 +</div>
  <svg width="80" height="80" viewBox="0 0 80 80"><circle cx="40" cy="40" r="37" fill="none" stroke="#0f3526" stroke-width="2.5"/><path d="M25 38h8v20h-8z M33 40l7-12c2-3 6-2 6 2l-1 8h9c3 0 4 3 3 5l-4 12c-1 2-2 3-4 3H33" fill="none" stroke="#0f3526" stroke-width="2.5" stroke-linejoin="round"/></svg></div>
<div class="abs stat" style="left:882px;top:1986px"><div class="num">400 +</div>
  <svg width="80" height="80" viewBox="0 0 80 80"><circle cx="40" cy="40" r="37" fill="none" stroke="#0f3526" stroke-width="2.5"/><path d="M25 38h8v20h-8z M33 40l7-12c2-3 6-2 6 2l-1 8h9c3 0 4 3 3 5l-4 12c-1 2-2 3-4 3H33" fill="none" stroke="#0f3526" stroke-width="2.5" stroke-linejoin="round"/></svg></div>
<div class="abs stat-label" style="left:143px">Lorem ipsum</div>
<div class="abs stat-label" style="left:390px">Lorem ipsum</div>
<div class="abs stat-label" style="left:636px">Lorem ipsum</div>
<div class="abs stat-label" style="left:882px">Lorem ipsum</div>

<section class="gallery">
  <h2 class="abs serif center"><span class="accent">Our</span> Work Gallery</h2>
  <svg class="abs chev" style="left:100px;top:2577px" viewBox="0 0 26 56"><path d="M22 2 L4 28 L22 54" fill="none" stroke="#222" stroke-width="2"/></svg>
  <svg class="abs chev" style="left:1075px;top:2577px" viewBox="0 0 26 56"><path d="M4 2 L22 28 L4 54" fill="none" stroke="#222" stroke-width="2"/></svg>
  <div class="abs before" role="img" aria-label="Before photo: overgrown hedge and patchy lawn"></div>
  <div class="abs after" role="img" aria-label="After photo: new timber fence with gate and stone paving"></div>
  <span class="abs ba-label" style="left:476px">Before</span>
  <span class="abs ba-label" style="left:648px">After</span>
  <svg class="abs ba-knob" viewBox="0 0 64 64"><circle cx="32" cy="32" r="32" fill="#5aae2e"/><path d="M29 24 L21 32 L29 40Z M35 24 L43 32 L35 40Z" fill="#fff"/></svg>
  <div class="abs thumbs">
    <div class="thumb" role="img" aria-label="Thumbnail: fenced patio" style="background:linear-gradient(180deg,#6d4e36,#9a8c80)"></div>
    <div class="thumb" role="img" aria-label="Thumbnail: timber fence and lawn" style="background:linear-gradient(180deg,#5a4a2a,#6e8a3c)"></div>
    <div class="thumb" role="img" aria-label="Thumbnail: fence run along garden" style="background:linear-gradient(180deg,#7a8aa0,#5a6e3a)"></div>
    <div class="thumb" role="img" aria-label="Thumbnail: stone patio slabs" style="background:linear-gradient(180deg,#6e8a4a,#c8c8c4)"></div>
    <div class="thumb" role="img" aria-label="Thumbnail: pergola over paving" style="background:linear-gradient(180deg,#6a4a38,#b8b2a8)"></div>
    <div class="thumb" role="img" aria-label="Thumbnail: gravel driveway" style="background:linear-gradient(180deg,#8a5a4a,#c8c6c0)"></div>
  </div>
</section>

<section class="abs testi">
  <h2 class="abs serif center">What Our <span class="accent">Clients are Saying</span></h2>
  <p class="abs lead center">Lorem ipsum dolor sit amet, consectetur adipiscing elit, sed do eiusmod tempor incididunt ut labore et dolore magna aliqua.</p>
  <div class="abs face" role="img" aria-label="Portrait photo of the client"></div>
  <blockquote class="abs">Lorem ipsum dolor sit amet, consectetur adipiscing elit, sed do eiusmod tempor incididunt ut labore et dolore magna aliqua. Ut enim ad minim veniam, quis nostrud exercitation ullamco laboris nisi ut aliquip ex ea commodo consequat. Duis aute irure dolor in reprehenderit.</blockquote>
  <span class="abs who">Maren Holloway CEO</span>
  <div class="abs arrows"><span>‹</span><span>›</span></div>
</section>

<footer>
  <div class="abs footer"></div>
  <svg class="abs footer-curve" viewBox="0 0 1200 70" preserveAspectRatio="none">
    <path d="M0 0 Q600 80 1200 0 L1200 70 L0 70Z" fill="#050505"/>
    <path d="M0 0 Q600 80 1200 0 L1200 8 Q600 88 0 8Z" fill="#5aae2e"/>
    <path d="M0 12 Q600 90 1200 12 L1200 22 Q600 100 0 22Z" fill="#0f3526"/>
  </svg>

  <svg class="abs" style="left:130px;top:3712px" width="80" height="70" viewBox="0 0 80 70">
    <path d="M10 8 L76 4 L40 38 Z M40 38 L44 24 L76 4" fill="none" stroke="#fff" stroke-width="2.5" stroke-linejoin="round"/>
    <path d="M28 30 C10 40 4 52 18 56 C28 58 24 46 12 52 C4 56 6 64 10 68" fill="none" stroke="#fff" stroke-width="1.6" stroke-dasharray="3 3"/>
  </svg>
  <div class="abs news-title">SUBSCRIBE<br>NEWSLETTER</div>
  <div class="abs news-box"><span class="news-input">Enter the Email</span><span class="sub-btn">SUBSCRIBE</span></div>
  <div class="abs rule" style="top:3808px"></div>

  <div class="abs foot-brand">BRACKWELL<small>LANDSCAPES</small></div>
  <div class="abs foot-social"><i class="dot"></i><i class="dot"></i><i class="dot"></i><i class="dot"></i></div>

  <div class="abs col" style="left:411px;top:3842px">
    <h4>QIUCK LINKS</h4>
    <ul><li>Home</li><li>About Us</li><li>Services</li><li>Gallery</li><li>Blog</li><li>Contact Us</li></ul>
  </div>
  <div class="abs col" style="left:650px;top:3842px">
    <h4>OUR SERVICES</h4>
    <ul><li>Driveways</li><li>Paving</li><li>Fencing</li></ul>
  </div>
  <div class="abs col contact" style="left:886px;top:3842px">
    <h4>CONTACT INFO</h4>
    <ul>
      <li><svg width="10" height="14" viewBox="0 0 10 14"><path d="M5 0a5 5 0 00-5 5c0 4 5 9 5 9s5-5 5-9a5 5 0 00-5-5zm0 7a2 2 0 110-4 2 2 0 010 4z" fill="#fff"/></svg>Lorem ipsum dolor sit amet<br>consectetur adip elit</li>
      <li><svg width="12" height="12" viewBox="0 0 24 24"><path d="M6.6 10.8a15 15 0 006.6 6.6l2.2-2.2c.3-.3.7-.4 1-.2 1.1.4 2.3.6 3.6.6.6 0 1 .4 1 1V20c0 .6-.4 1-1 1A17 17 0 013 4c0-.6.4-1 1-1h3.5c.6 0 1 .4 1 1 0 1.3.2 2.5.6 3.6.1.3 0 .7-.2 1z" fill="#fff"/></svg>07700 900 418</li>
      <li><svg width="13" height="10" viewBox="0 0 24 18"><path d="M0 1l12 8 12-8v17H0z M0 0h24L12 7z" fill="#fff"/></svg>hello@brackwell.example.com</li>
    </ul>
  </div>

  <div class="abs rule" style="top:4064px"></div>
  <span class="abs copy" style="left:116px">© Copyrights 2020 Brackwell Landscapes &nbsp;&nbsp;|&nbsp;&nbsp; All Rights Reserved</span>
  <span class="abs copy" style="left:805px">Privacy Policy &nbsp;&nbsp;|&nbsp;&nbsp; Terms &amp; Conditions</span>
</footer>

</body>
</html>
```